New Fun, Positive, energised looking Business Card Needed for High Achiever Coach

I am looking for a two sided full colour business card. I am self employed and have recently re branded my 1-2-1 work re-vitalising high achievers. My target client base for these cards is therefore high achievers - usually aged 40 -55, they are often entrepreneurs, CEO or work in banking and finance and 2/3 are male. I work with them on 90 day or 6 month coaching programs to help them live their success in a healthier, more sustainable and fulfiiled way. They pay for this privately so though they are corporate types the cards need not look 'corporate'. I want to portray the idea of transformation, vitality and re-connecting.
You can get a feel for the look I like on my new website: morvenlisk.co.uk
I want to use this logo with strapline (Re-Vitalising High Achievers) (I purchased off Logoharbor) and font/ colours (the turquoise and green).
Details to include on the card:
www.morvenlisk.co.uk
+44 7915 302618
morven@morvenlisk.co.uk
skype: morvenlisk
I'd also like to include:
Do you struggle to switch off? Want to be healthier and feel fitter? Want closer relationships? More clarity over the direction you are headed? I can help you do these things using integrated mind-body techniques. Visit morvenlisk.co.uk TODAY to apply for a FREE Breakthrough session.
BUT if that is too much text for a card I am open to advice/ammendments.
Updates
Thanks for your design - I am considering them. PLease change the wording to :

```html
<!DOCTYPE html>
<html lang="en">
<head>
<meta charset="utf-8">
<title>Morven Lisk – Business Card</title>
<link rel="stylesheet" href="https://fonts.googleapis.com/css2?family=Open+Sans:wght@400;700&display=swap">
<style>
  :root {
    --card-black: #0b0b0b;
    --turquoise: #1ba3c6;
    --green: #5cb85c;
    --white: #ffffff;
    --mark-grey: #4a4a4a;
    --backdrop: #e6e4e0;
  }
  * { box-sizing: border-box; margin: 0; padding: 0; }
  html, body { width: 1200px; height: 720px; overflow: hidden; }
  body {
    background: var(--backdrop);
    font-family: "Open Sans", sans-serif;
    position: relative;
  }
  .card {
    position: absolute;
    width: 560px;
    height: 320px;
    background: var(--card-black);
    overflow: hidden;
    box-shadow: 0 6px 18px rgba(0,0,0,0.18);
  }
  .card--front { left: 25px; top: 200px; }
  .card--back  { left: 615px; top: 200px; }

  .card__waves { position: absolute; inset: 0; width: 100%; height: 100%; }

  .brand {
    position: absolute;
    left: 30px;
    top: 118px;
    display: flex;
    align-items: center;
    gap: 10px;
  }
  .brand__dot {
    width: 14px; height: 14px;
    border-radius: 50%;
    background: var(--green);
  }
  .brand__name {
    font-weight: 700;
    font-size: 26px;
    line-height: 34px;
    color: var(--turquoise);
  }

  .contact {
    position: absolute;
    display: flex;
    align-items: center;
    gap: 7px;
    color: var(--white);
    font-size: 12.5px;
    line-height: 20px;
    white-space: nowrap;
  }
  .contact svg { width: 12px; height: 12px; flex: none; }
  .contact--phone { left: 362px; top: 106px; }
  .contact--email { left: 332px; top: 129px; }
  .contact--web   { left: 292px; top: 152px; }
  .contact--skype { left: 460px; top: 152px; }

  .back__mark {
    position: absolute;
    left: 200px; top: 80px;
    width: 160px; height: 160px;
    border-radius: 50%;
    background: var(--mark-grey);
    opacity: 0.45;
  }
  .pitch {
    position: absolute;
    inset: 0;
    display: flex;
    flex-direction: column;
    justify-content: center;
    align-items: center;
    text-align: center;
    color: var(--white);
    font-size: 15.5px;
    line-height: 21px;
  }
  .pitch p + p { margin-top: 8px; }
  .pitch strong { font-weight: 700; }
</style>
</head>
<body>

  <section class="card card--front" aria-label="Business card front">
    <svg class="card__waves" viewBox="0 0 560 320" aria-hidden="true">
      <path d="M0,300 C150,290 200,80 560,50 L560,320 L0,320 Z" fill="var(--turquoise)"/>
      <path d="M0,292 C150,282 200,72 560,42" fill="none" stroke="var(--white)" stroke-width="5"/>
      <path d="M0,285 C150,275 200,65 560,35" fill="none" stroke="var(--green)" stroke-width="5"/>
      <path d="M0,320 L0,306 C140,308 260,300 380,320 Z" fill="var(--card-black)"/>
      <path d="M0,306 C140,308 260,300 380,320" fill="none" stroke="var(--white)" stroke-width="3"/>
      <path d="M0,314 C120,316 220,312 300,320" fill="none" stroke="var(--green)" stroke-width="3"/>
    </svg>

    <div class="brand">
      <span class="brand__dot"></span>
      <span class="brand__name">Morven Lisk</span>
    </div>

    <div class="contact contact--phone">
      <svg viewBox="0 0 12 12"><circle cx="6" cy="6" r="5.5" fill="none" stroke="currentColor"/><path d="M4,3 L5,3 L5.5,4.5 L4.8,5 C5.2,6 6,6.8 7,7.2 L7.5,6.5 L9,7 L9,8 C6,8.5 3.5,6 4,3 Z" fill="currentColor"/></svg>
      +44 7915 302618
    </div>
    <div class="contact contact--email">
      <svg viewBox="0 0 12 12"><rect x="0.5" y="2.5" width="11" height="7" fill="none" stroke="currentColor"/><path d="M0.5,2.5 L6,7 L11.5,2.5" fill="none" stroke="currentColor"/></svg>
      morven@morvenlisk.co.uk
    </div>
    <div class="contact contact--web">
      <svg viewBox="0 0 12 12"><circle cx="6" cy="6" r="5.5" fill="none" stroke="currentColor"/><ellipse cx="6" cy="6" rx="2.4" ry="5.5" fill="none" stroke="currentColor"/><path d="M0.5,6 H11.5" stroke="currentColor"/></svg>
      www.morvenlisk.co.uk
    </div>
    <div class="contact contact--skype">
      <svg viewBox="0 0 12 12"><circle cx="6" cy="6" r="5.5" fill="currentColor"/></svg>
      morvenlisk
    </div>
  </section>

  <section class="card card--back" aria-label="Business card back">
    <div class="back__mark" aria-hidden="true"></div>
    <div class="pitch">
      <p>Do you struggle to switch off?<br>
        Want to be healthier and feel fitter?<br>
        Want closer relationships?<br>
        More clarity over the direction you are headed?</p>
      <p>I can help you do these things using integrated<br>
        mind-body techniques.</p>
      <p>Visit <strong>morvenlisk.co.uk</strong> TODAY to apply for a<br>
        FREE Breakthrough session.</p>
    </div>
  </section>

</body>
</html>
```